Easy Marinade Labels for Butchery Store

Need a set of labels designed for a Butchery Shop. They will sit in the top left corner of the packets as a triangle (7cm each side). Easy because the only major requirement is the label name and some small text saying "Please ask in store to see spec sheet for ingredients". Extra points for finding a fun way to incorporate the logo and/or images of food (garlic bulbs, chilli, spices ect) to enhance the label. List of Marinade Names below: GarlicPepper Mint & RosemarySatayBBQChilli Plum & GingerSundried Tomato & BasilBuffaloHoney SoyHoi-SinPer PeriSpicy CajunTeriyakiBlack Bean Ive also attached the logo and an example of how the label might sit on a packet of meat. Thanks

Target Market(s)

Butchery Deli Shop Customers

Industry/Entity Type

Food Store

Font styles to use
Serif
Sans Serif
Decorative
Other font styles liked:
• Fun font that isn't a generic Quellbrix Font?

Colors

Designer to choose colors to be used in the design.

Requirements
Must have
• Product Name
• Small text saying "Please ask in store to see spec sheet for ingredients"
Nice to have
• Photos of ingredients that would match that type of marinade - Chilli, Garlic, Spices.
• Fenly Oak Logo - not essential if it doesn't look good on the label / doesn't fit.

```html
<!DOCTYPE html>
<html lang="en">
<head>
<meta charset="utf-8">
<title>Garlic Pepper Marinade Label</title>
<link href="https://fonts.googleapis.com/css2?family=Barlow+Semi+Condensed:wght@500;700&family=Permanent+Marker&display=swap" rel="stylesheet">
<style>
  :root {
    --paper: #ffffff;
    --frame: #650805;
    --title-red: #ea1d0c;
    --note-red: #b3242e;
    --brand-red: #a3151a;
    --garlic-light: #f3eef2;
    --garlic-shade: #d9c8d6;
    --clove: #f5e9b8;
    --pepper-dark: #3a2a24;
    --pepper-red: #8b2434;
  }
  html, body {
    margin: 0;
    padding: 0;
    width: 1200px;
    height: 900px;
    overflow: hidden;
    background: var(--paper);
  }
  .label-canvas {
    display: block;
    width: 1200px;
    height: 900px;
  }
  .brand-name {
    font-family: "Barlow Semi Condensed", sans-serif;
    font-weight: 700;
    font-size: 30px;
    fill: var(--brand-red);
    letter-spacing: 1px;
  }
  .product-name {
    font-family: "Permanent Marker", cursive;
    font-size: 60px;
    fill: var(--title-red);
  }
  .ingredients-note {
    font-family: "Barlow Semi Condensed", sans-serif;
    font-weight: 500;
    font-size: 21px;
    fill: var(--note-red);
    letter-spacing: 2.6px;
  }
</style>
</head>
<body>
<svg class="label-canvas" viewBox="0 0 1200 900" xmlns="http://www.w3.org/2000/svg">
  <defs>
    <clipPath id="label-inner">
      <polygon points="617,228 189,655 1045,655"/>
    </clipPath>
    <radialGradient id="garlic-tone" cx="0.6" cy="0.35" r="0.7">
      <stop offset="0" stop-color="var(--garlic-light)"/>
      <stop offset="0.7" stop-color="var(--garlic-shade)"/>
      <stop offset="1" stop-color="var(--clove)"/>
    </radialGradient>
    <radialGradient id="pepper-tone" cx="0.5" cy="0.5" r="0.55">
      <stop offset="0" stop-color="var(--pepper-dark)"/>
      <stop offset="0.75" stop-color="var(--pepper-red)"/>
      <stop offset="1" stop-color="var(--pepper-red)" stop-opacity="0"/>
    </radialGradient>
  </defs>

  <polygon class="label-frame" points="617,206 151,671 1083,671" fill="var(--frame)"/>
  <polygon class="label-face" points="617,228 189,655 1045,655" fill="var(--paper)"/>

  <g clip-path="url(#label-inner)">
    <ellipse class="garlic-visual" role="img" aria-label="Garlic bulb with two peeled cloves"
             cx="400" cy="495" rx="105" ry="85" fill="url(#garlic-tone)"/>
    <ellipse class="pepper-visual" role="img" aria-label="Pile of mixed peppercorns"
             cx="835" cy="490" rx="95" ry="98" fill="url(#pepper-tone)"/>
  </g>

  <text class="brand-name" x="617" y="342" text-anchor="middle">Fenly Oak</text>

  <text class="product-name" x="620" y="485" text-anchor="middle">GARLIC</text>
  <text class="product-name" x="620" y="552" text-anchor="middle">PEPPER</text>

  <text class="ingredients-note" x="618" y="640" text-anchor="middle">PLEASE ASK IN STORE TO SEE SPEC SHEET FOR INGREDIENTS</text>
</svg>
</body>
</html>
```